Flat Belly Design Graphics for Social

I want to create 9 social media graphics (new Instagram size 4:5 (1080 x 1350 pixels) focusing on our Flat Belly Graphics, using the pics attached. Use the attached pics, NO RANDOM STOCK PHOTOGRAPHY. For the color scheme of the graphics, the color palette is attached. YOU MUST POST ALL 9 GRAPHICS IN ONE ENTRY.
Using the 3 titles below, create one set of graphics. 1) with all text, then for the others, use the pictures as detailed below in IMPORTANT:
1. Ten-Week Bright Morning Reboot
2. The Quick Garden Kitchen Menu Guide
3. Studio Habits for Lasting Energy Past Midlife - Zero Gym Needed
IMPORTANT:
Only use RK Pic 1 and RK Pic 2 with the title, Ten-Week Bright Morning Reboot
Only use meal plan1 and meal plan2 pics with the title, Quick Garden Kitchen Menu Guide
Only use studio habits 1 and studio habits 2 pics with the title, Studio Habits for Lasting Energy Past Midlife - Zero Gym Needed
women over 40

```html
<!DOCTYPE html>
<html lang="en">
<head>
<meta charset="utf-8">
<title>Social Graphics Set</title>
<link href="https://fonts.googleapis.com/css2?family=Oswald:wght@500;600;700&family=Montserrat:wght@700;800;900&display=swap" rel="stylesheet">
<style>
  :root {
    --board: #333333;
    --blush: #f7dde3;
    --blush-light: #fdf1f3;
    --pink: #c9548a;
    --pink-soft: #e9b4ca;
    --teal: #2a7369;
    --teal-dark: #264a45;
    --white: #ffffff;
    --food-dark: #4a3328;
    --food-warm: #c9694a;
    --food-green: #6b8f3e;
    --skin: #c89478;
  }
  * { margin: 0; padding: 0; box-sizing: border-box; }
  html, body { width: 980px; height: 1200px; overflow: hidden; background: var(--board); }
  .board { position: relative; width: 980px; height: 1200px; }
  .card {
    position: absolute; width: 287px; height: 358px; overflow: hidden;
    background: radial-gradient(ellipse at 70% 60%, var(--blush-light) 0%, var(--blush) 70%);
  }
  .col-1 { left: 36px; } .col-2 { left: 345px; } .col-3 { left: 653px; }
  .row-1 { top: 42px; } .row-2 { top: 419px; } .row-3 { top: 797px; }

  .abs { position: absolute; }
  .center { left: 0; right: 0; text-align: center; }
  .nowrap { white-space: nowrap; }
  .condensed { font-family: "Oswald", "Arial Narrow", sans-serif; font-weight: 700; text-transform: uppercase; line-height: 1; }
  .geo { font-family: "Montserrat", "Arial", sans-serif; font-weight: 800; line-height: 1; }
  .dashed::before, .dashed::after {
    content: ""; display: inline-block; width: 24px; height: 2px;
    background: currentColor; vertical-align: middle; margin: 0 6px;
  }
  .dash-left::before {
    content: ""; display: inline-block; width: 24px; height: 2px;
    background: currentColor; vertical-align: middle; margin-right: 8px;
  }

  .photo-person { background: linear-gradient(180deg, #e9d6d6 0%, var(--skin) 45%, #2a2a2e 100%); }
  .photo-friends { background: linear-gradient(135deg, #e8cfc3 0%, var(--skin) 50%, #7c9bb5 100%); }
  .photo-friends-wide { background: linear-gradient(160deg, #f1ece8 0%, #a46e54 45%, #3b2a25 100%); }
  .photo-food { background: linear-gradient(135deg, var(--food-dark) 0%, var(--food-warm) 40%, var(--food-green) 75%, var(--food-dark) 100%); }
  .photo-food-spread { background: linear-gradient(160deg, var(--food-green) 0%, var(--food-warm) 45%, var(--food-dark) 100%); }

  .rule { position: absolute; height: 1.5px; }
  .rule-pink { background: var(--pink); }
  .rule-teal { background: var(--teal); }
  .vertical { writing-mode: vertical-rl; transform: rotate(180deg); white-space: nowrap; }
</style>
</head>
<body>
<main class="board">

  <!-- Reboot, photo right -->
  <section class="card col-1 row-1">
    <div class="abs photo-person" role="img" aria-label="Smiling woman in a white cropped sweater pointing to her midsection" style="left:178px; top:58px; width:109px; height:300px;"></div>
    <div class="abs" style="left:0; top:40px; width:200px; height:34px; background:linear-gradient(90deg, var(--pink) 40%, rgba(201,84,138,0) 100%);"></div>
    <div class="abs condensed nowrap" style="left:24px; top:42px; font-size:28px; font-weight:600; color:var(--pink-soft);">Ten-Week</div>
    <div class="abs condensed nowrap" style="left:22px; top:80px; font-size:70px; color:var(--teal-dark);">Bright</div>
    <div class="abs condensed nowrap" style="left:22px; top:160px; font-size:50px; color:var(--teal-dark);">Morning</div>
    <div class="abs" style="left:0; top:278px; width:170px; height:42px; background:var(--pink-soft);"></div>
    <div class="abs condensed nowrap" style="left:24px; top:281px; font-size:36px; font-weight:600; color:var(--pink);">Reboot</div>
  </section>

  <!-- Menu guide, photo top -->
  <section class="card col-2 row-1">
    <div class="abs photo-food" role="img" aria-label="Overhead table of chicken, fruit, vegetables, grains and a written meal plan sheet" style="left:0; top:0; width:287px; height:191px;"></div>
    <div class="abs center geo dashed nowrap" style="top:212px; font-size:19px; font-weight:700; color:var(--pink);">The Quick</div>
    <div class="abs center condensed nowrap" style="top:240px; font-size:37px; color:var(--teal-dark);">Garden Kitchen</div>
    <div class="rule rule-teal" style="left:33px; right:33px; top:288px;"></div>
    <div class="abs center condensed nowrap" style="top:292px; font-size:46px; color:var(--teal);">Menu Guide</div>
  </section>

  <!-- Studio habits, vertical label left -->
  <section class="card col-3 row-1">
    <div class="abs center geo nowrap" style="top:22px; font-size:20px; color:var(--pink);">STUDIO HABITS</div>
    <div class="abs center geo dashed nowrap" style="top:46px; font-size:24px; color:var(--teal);">FOR LASTING</div>
    <div class="abs center condensed nowrap" style="top:76px; font-size:50px; color:var(--teal-dark);">Energy</div>
    <div class="rule rule-pink" style="left:27px; top:140px; width:1.5px; height:172px;"></div>
    <div class="abs condensed vertical" style="left:36px; top:140px; height:172px; font-size:27px; font-weight:600; color:var(--pink); text-align:center;">Past Midlife</div>
    <div class="abs" style="left:92px; top:278px; width:170px; height:35px; background:var(--pink); border-radius:0 6px 0 0;"></div>
    <div class="abs photo-friends" role="img" aria-label="Two women, one whispering to the other who looks surprised" style="left:104px; top:128px; width:150px; height:185px;"></div>
    <div class="abs center condensed nowrap" style="top:320px; font-size:24px; font-weight:600; color:var(--teal-dark);">Zero Gym Needed</div>
  </section>

  <!-- Reboot, photo left -->
  <section class="card col-1 row-2">
    <div class="abs photo-person" role="img" aria-label="Smiling woman in a white cropped sweater pointing to her midsection" style="left:0; top:34px; width:150px; height:246px;"></div>
    <div class="abs" style="left:100px; top:31px; width:187px; height:34px; background:linear-gradient(90deg, rgba(233,180,202,0) 0%, var(--pink-soft) 35%);"></div>
    <div class="abs geo dash-left nowrap" style="right:28px; top:34px; font-size:26px; color:var(--pink);">TEN-WEEK</div>
    <div class="abs condensed nowrap" style="right:28px; top:72px; font-size:68px; color:var(--teal-dark);">Bright</div>
    <div class="abs condensed nowrap" style="right:28px; top:152px; font-size:56px; color:var(--teal-dark);">Morning</div>
    <div class="rule rule-pink" style="left:115px; right:28px; top:228px;"></div>
    <div class="abs" style="left:0; top:280px; width:287px; height:52px; background:var(--pink);"></div>
    <div class="abs center geo nowrap" style="top:286px; font-size:40px; color:var(--white);">REBOOT</div>
  </section>

  <!-- Menu guide, photo middle -->
  <section class="card col-2 row-2">
    <div class="abs" style="left:0; top:12px; width:287px; height:36px; background:var(--pink-soft);"></div>
    <div class="abs center geo nowrap" style="top:17px; font-size:27px; color:var(--pink);">THE QUICK</div>
    <div class="abs center condensed nowrap" style="top:58px; font-size:40px; color:var(--teal-dark);">Garden Kitchen</div>
    <div class="abs photo-food-spread" role="img" aria-label="Fresh fruit, vegetables, salmon and eggs around a small meal plan notebook on a wooden table" style="left:0; top:115px; width:287px; height:191px;"></div>
    <div class="abs" style="left:0; top:306px; width:287px; height:52px; background:var(--white);"></div>
    <div class="abs center geo nowrap" style="top:314px; font-size:33px; color:var(--teal);">MENU GUIDE</div>
  </section>

  <!-- Studio habits, photo top -->
  <section class="card col-3 row-2">
    <div class="abs photo-friends-wide" role="img" aria-label="Close view of a woman whispering to a surprised friend" style="left:0; top:0; width:287px; height:181px;"></div>
    <div class="abs center geo nowrap" style="top:190px; font-size:21px; color:var(--pink);">STUDIO HABITS</div>
    <div class="abs center geo dashed nowrap" style="top:214px; font-size:22px; color:var(--teal);">FOR LASTING</div>
    <div class="abs center geo nowrap" style="top:240px; font-size:38px; color:var(--teal-dark);">ENERGY</div>
    <div class="abs center geo nowrap" style="top:282px; font-size:30px; color:var(--pink);">PAST MIDLIFE</div>
    <div class="abs" style="left:0; top:326px; width:287px; height:32px; background:var(--teal);"></div>
    <div class="abs center condensed dashed nowrap" style="top:329px; font-size:21px; font-weight:600; color:var(--white);">Zero Gym Needed</div>
  </section>

  <!-- Reboot, centred -->
  <section class="card col-1 row-3">
    <div class="abs center geo dashed nowrap" style="top:14px; font-size:28px; color:var(--pink);">TEN-WEEK</div>
    <div class="abs center geo nowrap" style="top:48px; font-size:52px; font-weight:900; color:var(--teal-dark);">BRIGHT</div>
    <div class="abs center geo nowrap" style="top:100px; font-size:45px; font-weight:900; color:var(--teal-dark);">MORNING</div>
    <div class="abs photo-person" role="img" aria-label="Smiling woman in a white cropped sweater pointing to her midsection with both hands" style="left:75px; top:145px; width:140px; height:163px;"></div>
    <div class="abs" style="left:0; top:308px; width:287px; height:50px; background:var(--teal);"></div>
    <div class="abs center geo nowrap" style="top:316px; font-size:34px; color:var(--white);">REBOOT</div>
  </section>

  <!-- Menu guide, photo bottom -->
  <section class="card col-2 row-3">
    <div class="abs center geo dashed nowrap" style="top:20px; font-size:19px; font-weight:700; color:var(--pink);">The Quick</div>
    <div class="abs center condensed nowrap" style="top:46px; font-size:38px; color:var(--teal-dark);">Garden Kitchen</div>
    <div class="rule rule-teal" style="left:32px; right:30px; top:104px;"></div>
    <div class="abs center geo nowrap" style="top:110px; font-size:34px; color:var(--teal);">MENU GUIDE</div>
    <div class="rule rule-teal" style="left:32px; right:30px; top:150px;"></div>
    <div class="abs photo-food" role="img" aria-label="Overhead table of chicken, fruit, vegetables, grains and a written meal plan sheet" style="left:0; top:167px; width:287px; height:191px;"></div>
  </section>

  <!-- Studio habits, vertical label right -->
  <section class="card col-3 row-3">
    <div class="abs" style="left:10px; top:0; width:267px; height:48px; background:var(--pink); border-radius:0 0 26px 26px;"></div>
    <div class="abs center geo nowrap" style="top:13px; font-size:22px; color:var(--white);">Studio Habits</div>
    <div class="abs center geo dashed nowrap" style="top:62px; font-size:25px; color:var(--teal-dark);">FOR LASTING</div>
    <div class="abs center condensed nowrap" style="top:92px; font-size:50px; color:var(--teal);">Energy</div>
    <div class="abs" style="left:18px; top:283px; width:190px; height:37px; background:var(--teal); border-radius:6px 0 0 6px;"></div>
    <div class="abs photo-friends" role="img" aria-label="Two women, one whispering to the other who looks surprised" style="left:35px; top:148px; width:160px; height:172px;"></div>
    <div class="abs" style="left:200px; top:148px; width:60px; height:172px; background:var(--pink);"></div>
    <div class="abs condensed vertical" style="left:211px; top:148px; height:172px; font-size:29px; font-weight:600; color:var(--white); text-align:center;">Past Midlife</div>
    <div class="abs center geo nowrap" style="top:330px; font-size:18px; color:var(--teal-dark);">ZERO GYM NEEDED</div>
  </section>

</main>
</body>
</html>
```